Redesign of business card for Cedar Ridge Mechanical

We are looking for a new design for our business cards for Cedar Ridge Mechanical. We are a plumbing & HVAC construction company, operating on the West Coast of Canada and USA. Logo attached.
Industry/Entity Type
Construction - Plumbing & HVAC
Contact Information for Business Card
Name, address, phone numbers, email, website address
Look and feel
Each slider illustrates characteristics of the customer's brand and the style your logo design should communicate.

```html
<!DOCTYPE html>
<html lang="en">
<head>
<meta charset="utf-8">
<title>Cedar Ridge Mechanical – Business Card</title>
<link href="https://fonts.googleapis.com/css2?family=Poppins:wght@300;400;700&display=swap" rel="stylesheet">
<style>
  :root {
    --backdrop: #232323;
    --card: #f0f0f0;
    --card-back: #e6e7e7;
    --ink: #111111;
    --rule: #1a1a1a;
    --emboss: #c9cbcb;
  }
  * { box-sizing: border-box; margin: 0; padding: 0; }
  html, body { width: 1200px; height: 780px; overflow: hidden; }
  body {
    background: var(--backdrop);
    font-family: "Poppins", sans-serif;
    color: var(--ink);
    position: relative;
  }
  .card {
    position: absolute;
    top: 235px;
    width: 540px;
    height: 309px;
    border-radius: 2px;
    overflow: hidden;
  }
  .card--front { left: 40px; background: var(--card); }
  .card--back { left: 620px; background: var(--card-back); }

  .card__band { position: absolute; left: 0; top: 0; width: 540px; height: 309px; }

  .brand {
    position: absolute;
    display: flex;
    align-items: center;
    gap: 10px;
    font-weight: 700;
    text-transform: uppercase;
    letter-spacing: 0.04em;
    line-height: 1.15;
  }
  .brand__square { border: 3px solid currentColor; flex: none; }
  .card--front .brand { left: 34px; top: 108px; width: 220px; font-size: 19px; color: var(--ink); }
  .card--front .brand__square { width: 30px; height: 30px; }

  .divider {
    position: absolute;
    left: 272px;
    top: 42px;
    width: 1px;
    height: 180px;
    background: var(--rule);
  }

  .contact { position: absolute; left: 296px; top: 38px; width: 230px; }
  .contact__name { font-size: 22px; line-height: 1.05; white-space: nowrap; }
  .contact__name strong { font-weight: 700; }
  .contact__name span { font-weight: 300; }
  .contact__title { font-size: 11px; font-weight: 400; margin-top: 2px; }
  .contact__address { font-size: 11px; font-weight: 300; margin-top: 14px; line-height: 1.4; }
  .contact__list { list-style: none; margin-top: 12px; font-size: 11px; font-weight: 300; }
  .contact__list li { display: flex; align-items: center; gap: 8px; line-height: 1.55; }
  .contact__icon { width: 11px; height: 11px; flex: none; }

  .card--back .brand {
    left: 0; right: 0; top: 0; bottom: 0;
    justify-content: center;
    font-size: 28px;
    color: var(--emboss);
  }
  .card--back .brand__square { width: 40px; height: 40px; }
</style>
</head>
<body>
  <section class="card card--front" aria-label="Business card front">
    <svg class="card__band" viewBox="0 0 540 309" aria-hidden="true">
      <path d="M0 262 L300 262 Q318 262 330 252 L352 236 Q362 230 374 230 L540 230 L540 246 L380 246 Q366 246 356 254 L338 268 Q324 280 306 280 L0 280 Z" fill="var(--ink)"/>
    </svg>

    <div class="brand"><span class="brand__square"></span><span>Cedar Ridge Mechanical</span></div>

    <div class="divider"></div>

    <div class="contact">
      <p class="contact__name"><strong>Marta</strong> <span>Kolarova</span></p>
      <p class="contact__title">Founder &amp; CEO</p>
      <p class="contact__address">1840 Harbor Ln. Suite 310<br>Vancouver, WA 98660</p>
      <ul class="contact__list">
        <li>
          <svg class="contact__icon" viewBox="0 0 12 12" aria-hidden="true"><path d="M3 1 L5 3.5 L4 5 Q5 7 7 8 L8.5 7 L11 9 L9.5 11 Q5 11 1 6.5 Q1 3 3 1 Z" fill="var(--ink)"/></svg>
          (360) 555-0147
        </li>
        <li>
          <svg class="contact__icon" viewBox="0 0 12 12" aria-hidden="true"><circle cx="6" cy="6" r="5.5" fill="var(--ink)"/><path d="M1 6 H11 M6 1 Q3 6 6 11 M6 1 Q9 6 6 11" stroke="var(--card)" stroke-width="0.8" fill="none"/></svg>
          info@cedarridgemech.com
        </li>
        <li>
          <svg class="contact__icon" viewBox="0 0 12 12" aria-hidden="true"><rect x="0.5" y="2.5" width="11" height="8" fill="var(--ink)"/><path d="M0.5 2.5 L6 7 L11.5 2.5" stroke="var(--card)" stroke-width="0.9" fill="none"/></svg>
          www.cedarridgemech.com
        </li>
      </ul>
    </div>
  </section>

  <section class="card card--back" aria-label="Business card back">
    <div class="brand"><span class="brand__square"></span><span>Cedar Ridge Mechanical</span></div>
  </section>
</body>
</html>
```